Drone company needs a brochure design

We would like a brochure design which compliments our existing logo, website and business card designs.

www.tallowbrook.com.au

```html
<!DOCTYPE html>
<html lang="en">
<head>
<meta charset="utf-8">
<title>Tallowbrook – Services &amp; About</title>
<link href="https://fonts.googleapis.com/css2?family=Exo+2:wght@600;700&family=Roboto:wght@400;700;900&display=swap" rel="stylesheet">
<style>
  :root {
    --bg-dark: #252527;
    --bg-mid: #2e2f32;
    --cyan: #4fd3f7;
    --ink-light: #ffffff;
    --icon-ink: #26272a;
    --divider: rgba(255,255,255,0.07);
  }
  html, body {
    margin: 0; padding: 0;
    width: 1200px; height: 849px;
    overflow: hidden;
    background: var(--bg-dark);
  }
  .spread {
    position: relative;
    width: 1200px; height: 849px;
    background: var(--bg-dark);
    font-family: "Roboto", Arial, sans-serif;
    color: var(--ink-light);
    overflow: hidden;
  }
  .backdrop { position: absolute; inset: 0; }
  .panel-divider {
    position: absolute; top: 0; width: 1px; height: 849px;
    background: var(--divider);
  }
  .service {
    position: absolute;
    width: 190px;
    text-align: center;
  }
  .service-icon {
    display: block;
    width: 77px; height: 77px;
    margin: 0 auto;
  }
  .service-title {
    margin: 0;
    font-family: "Exo 2", Arial, sans-serif;
    font-weight: 700;
    font-size: 12.6px;
    line-height: 15.4px;
    letter-spacing: 0.3px;
    color: var(--cyan);
  }
  .service-text {
    margin: 0;
    font-size: 11.6px;
    line-height: 14.3px;
  }
  .about {
    position: absolute;
    right: 52px;
    top: 532px;
    width: 330px;
    text-align: right;
  }
  .about-title {
    margin: 0 0 14px;
    font-weight: 900;
    font-size: 40px;
    line-height: 40px;
    color: var(--cyan);
    letter-spacing: 0.5px;
  }
  .about-text {
    margin: 0;
    font-size: 13.7px;
    line-height: 22.8px;
  }
</style>
</head>
<body>
<div class="spread">

  <svg class="backdrop" width="1200" height="849" viewBox="0 0 1200 849">
    <defs>
      <linearGradient id="suburbTones" x1="0" y1="0" x2="0" y2="1">
        <stop offset="0" stop-color="#dfe6ea"/>
        <stop offset="0.15" stop-color="#5f6c6a"/>
        <stop offset="0.35" stop-color="#3b4a35"/>
        <stop offset="0.7" stop-color="#7a5a46"/>
        <stop offset="1" stop-color="#8e7f6e"/>
      </linearGradient>
      <linearGradient id="droneTones" x1="0" y1="0" x2="0" y2="1">
        <stop offset="0" stop-color="#3aa39a"/>
        <stop offset="0.7" stop-color="#a9d8d1"/>
        <stop offset="0.8" stop-color="#6fa9a0"/>
        <stop offset="1" stop-color="#4d8f88"/>
      </linearGradient>
      <linearGradient id="stadiumTones" x1="0" y1="0" x2="0" y2="1">
        <stop offset="0" stop-color="#8fd7ef"/>
        <stop offset="0.3" stop-color="#cfe3e8"/>
        <stop offset="0.5" stop-color="#8c9a84"/>
        <stop offset="0.75" stop-color="#4d7d43"/>
        <stop offset="1" stop-color="#7f9a86"/>
      </linearGradient>
    </defs>

    <!-- left panel diagonal shading -->
    <polygon points="246,0 400,0 400,648 0,248" fill="var(--bg-mid)"/>

    <!-- photo areas -->
    <rect x="400" y="0" width="400" height="248" fill="url(#suburbTones)"
          role="img" aria-label="Aerial photo of a suburb with red-roofed houses and a distant city skyline"/>
    <polygon points="800,0 951,0 1197,247 800,248" fill="url(#droneTones)"
             role="img" aria-label="Photo of a camera drone flying above a river under a blue sky"/>
    <polygon points="400,249 1184,249 601,849 400,648" fill="url(#stadiumTones)"
             role="img" aria-label="Aerial photo of a city cricket stadium with floodlights and high-rise skyline"/>
  </svg>

  <div class="panel-divider" style="left:400px"></div>
  <div class="panel-divider" style="left:800px"></div>

  <!-- Row 1 -->
  <section class="service" style="left:11px; top:38px;">
    <svg class="service-icon" viewBox="0 0 77 77" aria-hidden="true">
      <circle cx="38.5" cy="38.5" r="38.5" fill="var(--cyan)"/>
      <g fill="var(--icon-ink)">
        <polygon points="17,34 30,26 38,31 45,27 60,36 57,38 45,31 33,38 33,49 17,49 17,37 15,38"/>
        <rect x="34" y="36" width="23" height="13"/>
      </g>
      <g fill="var(--cyan)">
        <rect x="21" y="38" width="4" height="4"/><rect x="27" y="38" width="4" height="4"/>
        <rect x="48" y="40" width="5" height="5"/>
      </g>
    </svg>
    <h2 class="service-title" style="margin-top:26px">REAL ESTATE</h2>
    <p class="service-text" style="margin-top:21px">Tallowbrook can<br>showcase important<br>factors like proximity to<br>the the coast, lakes,<br>schools, major transport,<br>CBD and the general feel<br>of an area.</p>
  </section>

  <section class="service" style="left:197px; top:38px;">
    <svg class="service-icon" viewBox="0 0 77 77" aria-hidden="true">
      <circle cx="38.5" cy="38.5" r="38.5" fill="var(--cyan)"/>
      <polygon points="28,19 42,16 49,19 49,57 42,60 28,57" fill="var(--icon-ink)"/>
      <g stroke="var(--cyan)" stroke-width="0.9">
        <line x1="30" y1="24" x2="41" y2="22"/><line x1="30" y1="29" x2="41" y2="27"/>
        <line x1="30" y1="34" x2="41" y2="32"/><line x1="30" y1="39" x2="41" y2="37"/>
        <line x1="30" y1="44" x2="41" y2="42"/><line x1="30" y1="49" x2="41" y2="47"/>
        <line x1="42" y1="18" x2="42" y2="59"/>
      </g>
    </svg>
    <h2 class="service-title" style="margin-top:18px">CONSTRUCTION<br>&amp; PROPERTY</h2>
    <p class="service-text" style="margin-top:6px">We can help you<br>affordably track the<br>progression of your<br>developments so you<br>can update your clients<br>with stunning aerial<br>photos and HD video.</p>
  </section>

  <!-- Row 2 -->
  <section class="service" style="left:11px; top:308px;">
    <svg class="service-icon" viewBox="0 0 77 77" aria-hidden="true">
      <circle cx="38.5" cy="38.5" r="38.5" fill="var(--cyan)"/>
      <rect x="18" y="20" width="41" height="29" rx="2" fill="none" stroke="var(--icon-ink)" stroke-width="3.5"/>
      <rect x="35" y="49" width="7" height="5" fill="var(--icon-ink)"/>
      <rect x="29" y="54" width="19" height="3" fill="var(--icon-ink)"/>
    </svg>
    <h2 class="service-title" style="margin-top:20px">MEDIA<br>&amp; ADVERTISING</h2>
    <p class="service-text" style="margin-top:9px">Aerial video and<br>photography are ideal<br>for websites and<br>promotioal publications<br>to show your products<br>or services with a new<br>perspective.</p>
  </section>

  <section class="service" style="left:197px; top:308px;">
    <svg class="service-icon" viewBox="0 0 77 77" aria-hidden="true">
      <circle cx="38.5" cy="38.5" r="38.5" fill="var(--cyan)"/>
      <circle cx="42" cy="35" r="13" fill="none" stroke="var(--icon-ink)" stroke-width="4"/>
      <line x1="32" y1="45" x2="20" y2="57" stroke="var(--icon-ink)" stroke-width="6" stroke-linecap="round"/>
      <path d="M36 34 a7 7 0 0 1 6 -7" fill="none" stroke="var(--icon-ink)" stroke-width="2"/>
    </svg>
    <h2 class="service-title" style="margin-top:20px">INSPECTION<br>&amp; ENVIRONMENT</h2>
    <p class="service-text" style="margin-top:8px">Our cameras can be<br>viewed in real-time and<br>we can take in-flight<br>instructions in order to<br>provide the perfect<br>vantage for their specific<br>needs</p>
  </section>

  <!-- Row 3 -->
  <section class="service" style="left:11px; top:577px;">
    <svg class="service-icon" viewBox="0 0 77 77" aria-hidden="true">
      <circle cx="38.5" cy="38.5" r="38.5" fill="var(--cyan)"/>
      <polygon points="18,40 48,33 60,41 30,55" fill="none" stroke="var(--icon-ink)" stroke-width="3" stroke-linejoin="round"/>
      <path d="M26 45 q8 -4 12 2 t12 -4" fill="none" stroke="var(--icon-ink)" stroke-width="2.5"/>
      <rect x="23" y="22" width="8" height="9" rx="1.5" fill="none" stroke="var(--icon-ink)" stroke-width="2.5"/>
      <line x1="27" y1="31" x2="27" y2="40" stroke="var(--icon-ink)" stroke-width="2.5"/>
    </svg>
    <h2 class="service-title" style="margin-top:19px">Survey<br>&amp; Mapping</h2>
    <p class="service-text" style="margin-top:9px">Reliable, timely survey<br>data to enhance<br>productivity or for<br>precise Geo-location.<br>Cost-effective alternative<br>to conventional aerial<br>surveys &amp; mapping.</p>
  </section>

  <section class="service" style="left:197px; top:576px;">
    <svg class="service-icon" viewBox="0 0 77 77" aria-hidden="true">
      <circle cx="38.5" cy="38.5" r="38.5" fill="var(--cyan)"/>
      <path d="M22 42 a7 7 0 0 1 3 -13 a10 10 0 0 1 18 -5 a8 8 0 0 1 12 8 a5 5 0 0 1 -1 10 z" fill="var(--icon-ink)"/>
      <g stroke="var(--icon-ink)" stroke-width="2.2" stroke-linecap="round">
        <line x1="27" y1="47" x2="24" y2="52"/><line x1="34" y1="47" x2="31" y2="52"/>
        <line x1="41" y1="47" x2="38" y2="52"/><line x1="48" y1="47" x2="45" y2="52"/>
        <line x1="24" y1="55" x2="21" y2="60"/><line x1="31" y1="55" x2="28" y2="60"/>
        <line x1="38" y1="55" x2="35" y2="60"/><line x1="45" y1="55" x2="42" y2="60"/>
      </g>
    </svg>
    <h2 class="service-title" style="margin-top:20px">Insurance<br>&amp; Risk</h2>
    <p class="service-text" style="margin-top:9px">We can work with local<br>insurance companies to<br>inspect damage caused<br>to land and properties.<br>Assisting assessors and<br>loss adjustors for claims.</p>
  </section>

  <!-- About -->
  <section class="about">
    <h1 class="about-title">ABOUT</h1>
    <p class="about-text">We provide premium aerial media<br>solutions using the latest<br>Unmanned Aerial Vehicles (UAV)<br>technology. Offering a combination of<br>stunning HD aerial filming and<br>breathtaking aerial photography for a variety<br>of different projects. The Tallowbrook team<br>offer a unique service that is bespoke to your<br>application and desired specification.</p>
  </section>

</div>
</body>
</html>
```